GlassHaven Artbook for Okanagan Region, British Columbia

Creating an art book: GlassHaven, for the Okanagan Wine Region in British Columbia, Canada. Would like smart, modern, clean and linear...cool, sexy urban, not ugly boring suburban... I need a cover that appeals to the wino in all of us! Title: GlassHaven -Marla Dovicki
Updates
Thank you all kindly for your efforts. I have added some files so that you can get a sense of my aesthetic...it's never easy trying to figure it out, is it? I will hopefully have dimensions of book soon...cheers, Marla
would anyone please design a giant wine bottle with the wine label that looks like a label but says glasshaven...just curious to see if it works as a design or not...thank you.
Target Market(s)
Designing this wine art book of quotes to wineries in Okanagan BC. Buyer is wine lover and tourist ready to spend his vacation bucks on this wonderful book!
Look and feel

```html
<!DOCTYPE html>
<html lang="en">
<head>
<meta charset="utf-8">
<title>GlassHaven – smart quotes</title>
<link href="https://fonts.googleapis.com/css2?family=Montserrat:wght@200;300;400&display=swap" rel="stylesheet">
<style>
  :root {
    --wine-red: #bd1622;
    --wine-red-soft: #c9414b;
    --paper: #ffffff;
  }
  html, body {
    margin: 0;
    padding: 0;
    width: 1200px;
    height: 886px;
    overflow: hidden;
    background: var(--paper);
  }
  .cover {
    position: relative;
    width: 1200px;
    height: 886px;
    background: var(--paper);
    font-family: "Montserrat", Arial, sans-serif;
  }
  .top-band {
    position: absolute;
    left: 290px;
    top: 41px;
    width: 633px;
    height: 94px;
    background: var(--wine-red);
  }
  .title {
    position: absolute;
    left: 290px;
    top: 152px;
    width: 633px;
    margin: 0;
    text-align: center;
    color: var(--wine-red);
    font-weight: 300;
    font-size: 48px;
    line-height: 1;
    letter-spacing: 25px;
    padding-left: 25px;
    box-sizing: border-box;
  }
  .subtitle {
    position: absolute;
    left: 290px;
    top: 207px;
    width: 633px;
    margin: 0;
    text-align: center;
    color: var(--wine-red);
    font-weight: 300;
    font-size: 34px;
    line-height: 1;
    letter-spacing: 10px;
    padding-left: 10px;
    box-sizing: border-box;
  }
  .bottle-panel {
    position: absolute;
    left: 290px;
    top: 258px;
    width: 633px;
    height: 588px;
    background: var(--wine-red);
  }
  .bottle-artwork {
    position: absolute;
    left: 22px;
    top: 92px;
    width: 592px;
    height: 496px;
    background: linear-gradient(90deg,
      var(--wine-red) 0%,
      var(--wine-red-soft) 25%,
      var(--paper) 42%,
      var(--paper) 58%,
      var(--wine-red-soft) 75%,
      var(--wine-red) 100%);
  }
  .author {
    position: absolute;
    left: 290px;
    top: 802px;
    width: 633px;
    margin: 0;
    text-align: center;
    color: var(--wine-red);
    font-weight: 300;
    font-size: 20px;
    letter-spacing: 0.5px;
    line-height: 1;
  }
</style>
</head>
<body>
  <main class="cover">
    <div class="top-band"></div>
    <h1 class="title">GlassHaven</h1>
    <p class="subtitle">smart quotes</p>
    <div class="bottle-panel">
      <div class="bottle-artwork" role="img" aria-label="Line illustration of three wine bottles side by side, the middle one solid white"></div>
    </div>
    <p class="author">MarlaDovicki</p>
  </main>
</body>
</html>
```